Modern Business Card for Larkwell 2018

Our company assumes the best about people. We are creating an online community of entrepreneurs and business leaders who struggle with marketing their business online.

This business card should POP! We recently got a new logo and are launching a new website next month, so our business cards should make a statement that feels:
-Fresh
-Smart
-Trustworthy
-Fun

Target Market(s)

small business owners, entrepreneurs

Industry/Entity Type

Digital Marketing

Contact Information for Business Card

Dimensions: 3.5" x 2"

Font styles to use
Sans Serif

Colors
f37122
ffffff

Requirements
Must have
• We need a business card with a modern, bold design. We will use one side of the card as a lead-generation offer, so text on one side will need to fit up to 140 characters. The business card should stick to our core colors (orange, black, and white).
Nice to have
• We think a vertical "portrait" design could be interesting.
Should not have
• Should not look like a traditional business card. The round icon should stand out from a distance.

```html
<!DOCTYPE html>
<html lang="en">
<head>
<meta charset="utf-8">
<title>Larkwell Business Card</title>
<link rel="stylesheet" href="https://fonts.googleapis.com/css2?family=Montserrat:wght@800&family=Roboto:wght@400;700&family=Permanent+Marker&family=Kaushan+Script&display=swap">
<style>
  :root {
    --orange: #f26a28;
    --black: #0d0d0d;
    --white: #ffffff;
    --card-front: #f1f1f1;
    --ink: #222222;
    --backdrop: #e8e5e1;
  }
  * { margin: 0; padding: 0; box-sizing: border-box; }
  html, body { width: 1200px; height: 960px; overflow: hidden; }
  body { background: var(--backdrop); position: relative; font-family: "Roboto", Arial, sans-serif; }

  .card {
    position: absolute;
    width: 600px;
    height: 343px;
    border-radius: 20px;
    overflow: hidden;
  }
  .card-front { left: 314px; top: 113px; background: var(--card-front); }
  .card-back { left: 311px; top: 472px; background: var(--orange); color: var(--white); text-align: center; }

  .brand-dot {
    position: absolute;
    left: 50%;
    width: 46px;
    height: 46px;
    margin-left: -23px;
    border-radius: 50%;
  }
  .card-front .brand-dot { top: 58px; background: var(--orange); }
  .card-back .brand-dot { top: 22px; background: var(--white); }

  .wordmark {
    position: absolute;
    top: 118px;
    left: 0; right: 0;
    text-align: center;
    font-family: "Montserrat", Arial, sans-serif;
    font-weight: 800;
    font-size: 44px;
    letter-spacing: 1px;
    color: var(--ink);
    line-height: 1;
  }
  .tagline {
    position: absolute;
    top: 166px;
    left: 0; right: 0;
    text-align: center;
    font-family: "Permanent Marker", cursive;
    font-size: 14px;
    letter-spacing: 1px;
    color: var(--ink);
  }
  .email {
    position: absolute;
    top: 195px;
    left: 0; right: 0;
    text-align: center;
    font-size: 15px;
    letter-spacing: 2px;
    color: var(--black);
  }

  .name-band { position: absolute; left: 0; top: 241px; width: 600px; height: 65px; }
  .name-band svg { position: absolute; inset: 0; }
  .person-name {
    position: absolute;
    left: 32px; top: 8px;
    font-family: "Kaushan Script", cursive;
    font-size: 36px;
    color: var(--white);
    white-space: nowrap;
  }
  .person-role {
    position: absolute;
    left: 334px; top: 22px;
    font-size: 17px;
    letter-spacing: 0.5px;
    color: var(--white);
    white-space: nowrap;
  }

  .offer-headline {
    position: absolute;
    top: 76px; left: 0; right: 0;
    font-weight: 700;
    font-size: 19px;
    line-height: 21px;
  }
  .offer-text {
    position: absolute;
    top: 149px; left: 0; right: 0;
    font-size: 15px;
    line-height: 20px;
  }
  .offer-link { display: block; font-weight: 700; font-size: 18px; line-height: 22px; }

  .note-box {
    position: absolute;
    left: 20px; top: 224px;
    width: 557px; height: 101px;
    background: var(--white);
    border-radius: 18px;
  }
  .note-line {
    position: absolute;
    left: 24px; right: 27px;
    height: 1px;
    background: var(--black);
  }
  .note-line.first { top: 31px; }
  .note-line.second { top: 71px; }
</style>
</head>
<body>
  <section class="card card-front" aria-label="Card front">
    <span class="brand-dot"></span>
    <h1 class="wordmark">LARKWELL</h1>
    <p class="tagline">TELL STORIES THAT INSPIRE ACTION</p>
    <p class="email">dana@larkwellnow.com</p>
    <div class="name-band">
      <svg width="600" height="65" viewBox="0 0 600 65" aria-hidden="true">
        <polygon points="0,0 320,0 300,65 0,65" fill="var(--black)"/>
        <polygon points="324,0 600,0 600,65 304,65" fill="var(--orange)"/>
      </svg>
      <span class="person-name">DANA MORROW</span>
      <span class="person-role">STORY MARKETING COACH</span>
    </div>
  </section>

  <section class="card card-back" aria-label="Card back">
    <span class="brand-dot"></span>
    <h2 class="offer-headline">REACH MORE PEOPLE.<br>MAKE MORE MONEY.<br>CREATE MORE IMPACT.</h2>
    <p class="offer-text">Get your free Larkwell, Starter Package and our<br>marketing guide today at
      <span class="offer-link">Larkwellnow.com/start</span></p>
    <div class="note-box">
      <span class="note-line first"></span>
      <span class="note-line second"></span>
    </div>
  </section>
</body>
</html>
```